Verpackungen für Parfum-Proben
Besten Dank! Das Team ist begeistert - also bin ich es auch und wir freuen uns schon, unsere Parfum Proben in Zukunft in diesem tollen Design weitergeben zu können! Danke!
Zielgruppe
Hallo allerseits! Wir sind im Direktvertrieb in den Bereichen Parfum & Kosmetik tätig.
Aufgabenstellung
Für unsere Parfum-Proben benötige ich ein ansprechendes, modernes Design.
Das Design muss relativ neutral gehalten werden, da die Blister sowohl für Herren- als auch Damenproben verwendet werden.
Auf Vorder- und Rückseite soll unser Team-Logo (NaseNomade®) sichtbar sein (Vorderseite größer, Rückseite kleiner).
Auf der linken Innenseite sollte Plätz für einen netten Spruch (den ich mir noch überlege) sein.
Auf der Rückseite muss Platz (weißes / helles Feld) für einen Stempel und/oder Aufkleber (Kontaktdaten des Distributors) sein.
Unser Logo ist Lila - Das farbliche Design sollte dazu passen.
Bei Fragen, einfach Nachricht :)
Daten:
Endformat: 133 x 74 mm
Datenformat: 139 x 80 mm
1-teilig, gestanzt, genutet, einseitig geklebt geliefert
Bitte verwenden Sie für positive Schriftstärken mindestens 9pt (ca. 3,17mm) und bei negativen Schriftstärken mindestens 13pt (ca. 4,59mm).
Abmessungen / Druck- / Designvorlage, Logo, etc.: https://dateiwolke-beispiel.de/ordner/X7pLrT2k#v9wQe4nZb6Hs1Ym_d8cKfa

```html
<!DOCTYPE html>
<html lang="de">
<head>
<meta charset="utf-8">
<title>NaseNomade – Probenblister</title>
<link rel="stylesheet" href="https://fonts.googleapis.com/css2?family=Encode+Sans+Condensed:wght@300;400&display=swap">
<style>
  :root {
    --canvas: #e6e6e6;
    --brand: #7656b0;
    --sky-top: #dfe8ea;
    --sky-haze: #ece6ea;
    --horizon: #e6cfd6;
    --sea-light: #b4d3d4;
    --sea-deep: #8fbcc0;
    --boards: #c9dcdc;
    --boards-dark: #6f8588;
    --field: #ffffff;
    --quote-disc: rgba(236, 236, 244, 0.72);
  }
  * { box-sizing: border-box; margin: 0; padding: 0; }
  html, body {
    width: 1200px; height: 2330px; overflow: hidden;
    background: var(--canvas);
    font-family: "Encode Sans Condensed", "Arial Narrow", sans-serif;
  }
  .sheet {
    position: absolute; left: 60px; width: 1080px; height: 600px;
    overflow: hidden;
    box-shadow: 0 4px 18px rgba(0,0,0,0.12);
  }
  .sheet--outside { top: 440px; }
  .sheet--inside  { top: 1290px; }

  .photo {
    position: absolute; inset: 0;
    background: linear-gradient(180deg,
      var(--sky-top) 0%, var(--sky-haze) 28%, var(--horizon) 40%,
      var(--sea-light) 46%, var(--sea-deep) 70%,
      var(--boards) 80%, var(--boards-dark) 88%, var(--boards) 94%, var(--boards-dark) 100%);
  }

  .brand {
    position: absolute; display: flex; align-items: center;
    color: var(--brand); font-weight: 400; white-space: nowrap;
  }
  .brand__dot { border-radius: 50%; background: var(--brand); flex: none; }
  .brand--large { left: 110px; top: 140px; font-size: 40px; gap: 12px; }
  .brand--large .brand__dot { width: 22px; height: 22px; }
  .brand--small { font-size: 26px; gap: 8px; }
  .brand--small .brand__dot { width: 14px; height: 14px; }
  .sheet--outside .brand--small { left: 840px; top: 232px; }
  .sheet--inside .brand--small { left: 880px; top: 52px; }

  .stamp-field {
    position: absolute; left: 56px; top: 432px; width: 372px; height: 140px;
    background: var(--field); border-radius: 10px;
  }

  .quote {
    position: absolute; left: 48px; top: 150px; width: 420px; height: 420px;
    border-radius: 50%; background: var(--quote-disc);
    display: flex; flex-direction: column; align-items: center; justify-content: center;
    color: var(--brand); text-align: center; font-weight: 300;
  }
  .quote__text { font-size: 41px; line-height: 1.42; }
  .quote__author { font-size: 30px; margin-top: 22px; }
</style>
</head>
<body>
  <section class="sheet sheet--outside" aria-label="Außenseite">
    <div class="photo" role="img" aria-label="Foto: Paar in Umarmung auf einem hellen Holzsteg am Meer bei Dämmerung"></div>
    <div class="brand brand--large"><span class="brand__dot"></span>Die NaseNomade</div>
    <div class="brand brand--small"><span class="brand__dot"></span>Die NaseNomade</div>
    <div class="stamp-field" aria-label="Feld für Stempel oder Aufkleber"></div>
  </section>

  <section class="sheet sheet--inside" aria-label="Innenseite">
    <div class="photo" role="img" aria-label="Foto: Paar sitzt eng beieinander auf einem Holzsteg vor dem Meer"></div>
    <div class="quote">
      <p class="quote__text">Ein Parfüm ist immer<br>auch ein Statement<br>über das, was du bist.</p>
      <p class="quote__author">Lena Hartwig</p>
    </div>
    <div class="brand brand--small"><span class="brand__dot"></span>Die NaseNomade</div>
  </section>
</body>
</html>
```